Tarvolen - Tarvolen Border Flow Reshaping Trade

Web Design for international start-up, which is automating customs clearance processes for forwarding companies by applying a web application, which is operating with artificial intelligence and robotic process automation. Tarvolen pursues the vision of supporting forwarding companies successfully in becoming digital masters and co-creates innovative software solutions with all participants (ex- and importers of goods) along value-added chains. With intelligent/smart/digital customs clearance software or in other words, a virtual customs clearance roboter tailord to the customers needs, we are transforming businesses. The website could look like this:

https://www.plomix.com/uk-en/index.php
or
https://sitebrenna.com/theme/halvering

Please use colours and designs you think would be the best fit. These websites are just here to give you an idea of how the webdesign could look like. Use the attached logo design as a basis for further web design. You can use the provided pictures, but you can also use your own ones, if you think they are better suited. But please take care, that they have a high resolution quality.

Description of Website: The website is transparent and modern. It provides seven pages such as homepage, products, web app, the about us, working at Tarvolen, News, contact us and search results page. The homepage or landing page should be filled with a short description of the company, what Tarvolen is doing, how they will support its customers and will also include a video of the provided solution. Products provide obviously information about different products and their characteristics. Web app page includes information about principles and technologies that get the software going. The about us page includes unique advantages and value propositions for customers and the contact us, as the name already says, will provide contact information and possibilities to contact us. The rest is also obvious (for additional information look up the website of PLX, priorly provided link - the page is also available in english).

If you have any questions, I am happy to answer them any time.
Updates

I have to think about the text that I want to have included into the design and hadn't have the time to compose it.

Target Market(s)

Forwarding Companies, Ex-/Importers

Industry/Entity Type

It Company

Number of Pages Required

5+ page

Requirements
Must have
• The web design should be designes according to the attached logo of Tarvolen.

```html
<!DOCTYPE html>
<html lang="en">
<head>
<meta charset="utf-8">
<title>Tarvolen – Border Flow Reshaping Trade</title>
<link rel="stylesheet" href="https://fonts.googleapis.com/css2?family=Roboto:wght@300;400;500;700&display=swap">
<style>
:root{
  --blue:#2f4b9e;
  --blue-deep:#233d8c;
  --cyan:#27b5dc;
  --teal:#1b8aa6;
  --ink:#1d1d1d;
  --grey:#5a5a5a;
  --pale:#f3f5f9;
  --footer:#2a2f38;
  --white:#ffffff;
}
*{margin:0;padding:0;box-sizing:border-box}
html,body{width:1200px;height:3622px;overflow:hidden}
body{position:relative;font-family:"Roboto",sans-serif;color:var(--ink);background:var(--white)}
.abs{position:absolute}
a{color:inherit;text-decoration:none}

/* header */
.site-header{left:0;top:0;width:1200px;height:137px;background:var(--white);z-index:5}
.brand{left:88px;top:18px}
.brand-name{font-size:66px;font-weight:500;color:var(--blue);letter-spacing:1px;line-height:1}
.brand-tag{font-size:19px;font-weight:300;color:var(--grey);text-align:right;margin-top:2px}
.contact-chip{top:32px;display:flex;align-items:center;gap:10px}
.chip-icon{width:48px;height:48px;border-radius:50%;background:linear-gradient(135deg,var(--cyan),var(--blue));display:flex;align-items:center;justify-content:center}
.chip-label{font-size:13px;font-weight:700;color:var(--blue)}
.chip-value{font-size:13px;color:var(--ink);margin-top:3px}
.main-nav{top:100px;left:504px;display:flex;gap:30px;font-size:17px}

/* hero */
.hero{left:0;top:137px;width:1200px;height:628px;background:linear-gradient(115deg,#c9d0da 0%,#eef1f5 40%,#f7f8fa 70%,#cdd4de 100%)}
.hero-title{left:551px;top:325px;font-size:35px;font-weight:500;color:var(--blue)}
.hero-text{left:551px;top:373px;width:560px;font-size:22px;line-height:41px;color:#222}
.btn{display:flex;align-items:center;justify-content:center;gap:10px;border-radius:28px;color:var(--white);font-weight:500;font-size:19px}
.btn-blue{background:linear-gradient(90deg,var(--blue),var(--cyan))}
.btn-cyan{background:var(--cyan)}
.btn-navy{background:var(--blue);border:2px solid var(--cyan)}
.btn-ghost{border:3px solid var(--white);background:transparent}
.arrow{width:19px;height:19px}
.dots{left:551px;top:540px;display:flex;gap:6px}
.dots span{width:16px;height:16px;border-radius:50%;background:var(--cyan)}
.dots span.on{background:var(--white);border:4px solid var(--cyan)}

/* welcome */
.welcome{left:0;top:765px;width:1200px;height:865px;background:linear-gradient(180deg,#f6f7fa,#eef1f6)}
.section-title{font-size:36px;font-weight:500;text-transform:uppercase}
.section-title .lt{color:var(--cyan)}
.section-title .dk{color:var(--blue)}
.welcome-title{left:0;width:1200px;top:835px;text-align:center}
.welcome-text{left:110px;width:980px;top:898px;text-align:center;font-size:15px;line-height:36px}
.mark-block{left:90px;top:1238px;width:275px;height:312px;display:flex;align-items:center;gap:12px}
.mark-block .sq{width:26px;height:26px;background:var(--blue)}
.mark-block .word{font-size:54px;font-weight:500;color:var(--blue)}
.doing-title{left:511px;top:1238px}
.doing-text{left:511px;top:1296px;width:600px;font-size:15px;line-height:34px;text-align:justify}

/* how it works */
.how{left:0;top:1630px;width:1200px;height:830px;background:linear-gradient(180deg,#1b8fa8 0%,#1d6fa0 50%,#2a4e9c 100%)}
.how-title{left:0;width:1200px;top:1782px;text-align:center;color:var(--white)}
.how-sub{left:90px;top:1907px;font-size:27px;font-weight:500;color:var(--white);text-transform:uppercase}
.how-text{left:90px;top:1956px;width:536px;font-size:16px;line-height:34px;color:var(--white);text-align:justify}
.video{left:673px;top:1856px;width:444px;height:444px;border-radius:50%;border:10px solid #3553a8;background:radial-gradient(circle at 50% 45%,#f2f2f2 0%,#d8dbe0 55%,#a8adb8 100%)}
.play{left:860px;top:2052px;width:76px;height:52px;border-radius:12px;background:var(--blue);display:flex;align-items:center;justify-content:center}

/* contact */
.contact{left:0;top:2460px;width:1200px;height:720px;background:linear-gradient(180deg,#fbfbfc,#eef0f3)}
.contact-title{left:0;width:1200px;top:2532px;text-align:center}
.contact-lead{left:0;width:1200px;top:2590px;text-align:center;font-size:17px}
.info{top:2641px;width:300px;text-align:center;color:#555;font-size:17px;line-height:29px}
.info .ic{width:84px;height:84px;border-radius:50%;background:linear-gradient(135deg,var(--cyan),var(--blue));margin:0 auto 18px;display:flex;align-items:center;justify-content:center}
.field{height:36px;background:var(--white);border:1px solid #e2e4e8;font-size:11px;color:#555;padding:11px 16px}
.submit{left:511px;top:3045px;width:178px;height:48px;background:linear-gradient(90deg,var(--blue),var(--cyan));color:var(--white);font-size:17px;font-weight:500;display:flex;align-items:center;justify-content:center;gap:8px}

/* footer */
.site-footer{left:0;top:3180px;width:1200px;height:442px;background:linear-gradient(180deg,#39404b,#1f242c)}
.footer-brand{left:0;width:1200px;top:3335px;text-align:center}
.footer-brand .brand-name{font-size:86px}
.footer-brand .brand-tag{font-size:21px;text-align:center;color:#7d8593;margin-top:-4px}
.footer-nav{left:0;width:1200px;top:3470px;text-align:center;font-size:18px;color:var(--white)}
.footer-nav span{margin:0 10px}
.copyright{left:0;width:1200px;top:3514px;text-align:center;font-size:15px;color:var(--white)}
.social{left:530px;top:3551px;display:flex;gap:6px}
.social span{width:31px;height:31px;border-radius:50%;border:2px solid var(--white)}
</style>
</head>
<body>

<header class="abs site-header">
  <div class="abs brand">
    <div class="brand-name">Tarvolen</div>
    <div class="brand-tag">Border Flow Reshaping Trade</div>
  </div>
  <div class="abs contact-chip" style="left:560px">
    <div class="chip-icon"><svg width="24" height="24" viewBox="0 0 24 24"><path d="M6 3l4 4-2 3a12 12 0 006 6l3-2 4 4-3 3C10 21 3 14 3 6z" fill="#fff"/></svg></div>
    <div><div class="chip-label">CALL US</div><div class="chip-value">888 888 8888</div></div>
  </div>
  <div class="abs contact-chip" style="left:726px">
    <div class="chip-icon"><svg width="24" height="24" viewBox="0 0 24 24"><rect x="3" y="6" width="18" height="13" fill="none" stroke="#fff" stroke-width="2"/><path d="M3 6l9 7 9-7" fill="none" stroke="#fff" stroke-width="2"/></svg></div>
    <div><div class="chip-label">EMAIL US</div><div class="chip-value">Info@tarvolen.com</div></div>
  </div>
  <div class="abs contact-chip" style="left:928px">
    <div class="chip-icon"><svg width="24" height="24" viewBox="0 0 24 24"><circle cx="10" cy="10" r="6" fill="none" stroke="#fff" stroke-width="2"/><path d="M15 15l6 6" stroke="#fff" stroke-width="2.5"/></svg></div>
    <div><div class="chip-label">SEARCH</div><div class="chip-value">Enter Search here...</div></div>
  </div>
  <nav class="abs main-nav">
    <a href="#">Products</a><a href="#">Web App</a><a href="#">About Us</a><a href="#">Working At Tarvolen</a><a href="#">News</a><a href="#">Contact</a>
  </nav>
</header>

<section class="abs hero" role="img" aria-label="Upward view of glass office towers against a pale sky"></section>
<h1 class="abs hero-title">BORDER FLOW RESHAPING TRADE</h1>
<p class="abs hero-text">Lorem ipsum dolor sit amet, consectetur adipiscing elit, sed do eiusmod tempor incididunt facilisis.</p>
<a class="abs btn btn-blue" href="#" style="left:551px;top:465px;width:206px;height:52px">READ MORE <svg class="arrow" viewBox="0 0 20 20"><circle cx="10" cy="10" r="10" fill="#fff"/><path d="M5 10h8M10 6l4 4-4 4" stroke="#2f4b9e" stroke-width="2.4" fill="none"/></svg></a>
<div class="abs dots"><span></span><span class="on"></span><span></span><span></span><span></span></div>

<section class="abs welcome" role="img" aria-label="Faint background of steel building framework"></section>
<svg class="abs" style="left:0;top:680px" width="1200" height="100" viewBox="0 0 1200 100">
  <path d="M0 85 Q600 0 1200 85 L1200 100 L0 100Z" fill="#f6f7fa"/>
  <path d="M40 78 Q600 0 1160 78" stroke="#2f4b9e" stroke-width="7" fill="none"/>
  <circle cx="600" cy="17" r="24" fill="#fff" stroke="#27b5dc" stroke-width="3"/>
  <circle cx="600" cy="17" r="8" fill="#2f4b9e"/>
</svg>
<h2 class="abs section-title welcome-title"><span class="lt">Welcome to</span> <span class="dk">Tarvolen</span></h2>
<p class="abs welcome-text">Sed ut perspiciatis unde omnis iste natus error sit voluptatem accusantium doloremque laudantium, totam rem aperiam, eaque ipsa quae ab illo inventore veritatis et quasi architecto beatae vitae dicta sunt explicabo. Nemo enim ipsam voluptatem quia voluptas sit aspernatur aut odit aut fugit, sed quia consequuntur magni dolores eos qui ratione voluptatem sequi nesciunt.</p>
<a class="abs btn btn-cyan" href="#" style="left:386px;top:1025px;width:206px;height:54px">READ MORE <svg class="arrow" viewBox="0 0 20 20"><circle cx="10" cy="10" r="10" fill="#fff"/><path d="M5 10h8M10 6l4 4-4 4" stroke="#27b5dc" stroke-width="2.4" fill="none"/></svg></a>
<a class="abs btn btn-navy" href="#" style="left:609px;top:1025px;width:206px;height:54px">CONTACT US <svg class="arrow" viewBox="0 0 20 20"><circle cx="10" cy="10" r="10" fill="#fff"/><path d="M5 10h8M10 6l4 4-4 4" stroke="#2f4b9e" stroke-width="2.4" fill="none"/></svg></a>

<div class="abs mark-block"><span class="sq"></span><span class="word">Tarvolen</span></div>
<h2 class="abs section-title doing-title"><span class="lt">What</span> <span class="dk">Tarvolen is doing</span></h2>
<p class="abs doing-text">Sed ut perspiciatis unde omnis iste natus error sit voluptatem accusantium doloremque laudantium, totam rem aperiam, eaque ipsa quae ab illo inventore veritatis et quasi architecto beatae vitae dicta sunt explicabo. Nemo enim ipsam voluptatem quia voluptas sit aspernatur aut odit aut fugit, sed quia consequuntur magni dolores eos qui ratione voluptatem sequi nesciunt.</p>
<a class="abs btn btn-blue" href="#" style="left:511px;top:1484px;width:206px;height:54px">READ MORE <svg class="arrow" viewBox="0 0 20 20"><circle cx="10" cy="10" r="10" fill="#fff"/><path d="M5 10h8M10 6l4 4-4 4" stroke="#2f4b9e" stroke-width="2.4" fill="none"/></svg></a>

<section class="abs how"></section>
<svg class="abs" style="left:0;top:1620px" width="1200" height="100" viewBox="0 0 1200 100">
  <path d="M0 0 L1200 0 L1200 20 Q600 90 0 20Z" fill="#eef1f6"/>
  <path d="M80 30 Q600 100 1120 30" stroke="#27b5dc" stroke-width="6" fill="none"/>
</svg>
<h2 class="abs section-title how-title">How it works</h2>
<h3 class="abs how-sub">How they will support its customers</h3>
<p class="abs how-text">Sed ut perspiciatis unde omnis iste natus error sit voluptatem accusantium doloremque laudantium, totam rem aperiam, eaque ipsa quae ab illo inventore veritatis et quasi architecto beatae vitae dicta sunt explicabo. Nemo enim ipsam voluptatem quia voluptas sit aspernatur aut odit aut fugit, sed quia consequuntur magni dolores eos qui ratione voluptatem sequi nesciunt.</p>
<a class="abs btn btn-ghost" href="#" style="left:90px;top:2178px;width:205px;height:54px">Read More <svg class="arrow" viewBox="0 0 20 20"><circle cx="10" cy="10" r="10" fill="#fff"/><path d="M5 10h8M10 6l4 4-4 4" stroke="#2a4e9c" stroke-width="2.4" fill="none"/></svg></a>
<div class="abs video" role="img" aria-label="Video still of a team discussing around a monitor in a bright office"></div>
<div class="abs play"><svg width="24" height="26" viewBox="0 0 24 26"><path d="M2 1l21 12L2 25z" fill="#fff"/></svg></div>

<section class="abs contact" role="img" aria-label="Faint city skyline behind the contact area"></section>
<svg class="abs" style="left:0;top:2370px" width="1200" height="100" viewBox="0 0 1200 100">
  <path d="M0 100 L0 90 Q600 0 1200 90 L1200 100Z" fill="#fbfbfc"/>
  <path d="M120 70 Q600 0 1080 70" stroke="#2f4b9e" stroke-width="6" fill="none"/>
</svg>
<h2 class="abs section-title contact-title"><span class="lt">Contact us</span></h2>
<p class="abs contact-lead">Contact us for more information</p>
<div class="abs info" style="left:151px">
  <div class="ic"><svg width="40" height="40" viewBox="0 0 40 40"><path d="M20 6a9 9 0 00-9 9c0 7 9 16 9 16s9-9 9-16a9 9 0 00-9-9z" fill="none" stroke="#fff" stroke-width="2"/><circle cx="20" cy="15" r="3.5" fill="none" stroke="#fff" stroke-width="2"/></svg></div>
  Location:<br>517 Alder Lane, Westbrook
</div>
<div class="abs info" style="left:458px;top:2639px">
  <div class="ic"><svg width="40" height="40" viewBox="0 0 24 24"><path d="M6 3l4 4-2 3a12 12 0 006 6l3-2 4 4-3 3C10 21 3 14 3 6z" fill="none" stroke="#fff" stroke-width="1.6"/></svg></div>
  Phone:<br>888 888 8888
</div>
<div class="abs info" style="left:763px;top:2645px">
  <div class="ic"><svg width="44" height="44" viewBox="0 0 24 24"><rect x="3" y="6" width="18" height="13" fill="none" stroke="#fff" stroke-width="1.4"/><path d="M3 6l9 7 9-7M3 19l7-6M21 19l-7-6" fill="none" stroke="#fff" stroke-width="1.4"/></svg></div>
  Email:<br>info@tarvolen.com
</div>
<form>
  <div class="abs field" style="left:163px;top:2830px;width:427px">&#9679; First Name</div>
  <div class="abs field" style="left:610px;top:2830px;width:428px">&#9679; Last Name</div>
  <div class="abs field" style="left:163px;top:2884px;width:427px">&#9632; Company</div>
  <div class="abs field" style="left:610px;top:2884px;width:428px;height:146px">&#9679; Message :</div>
  <div class="abs field" style="left:163px;top:2938px;width:427px">&#9633; Email Address</div>
  <div class="abs field" style="left:163px;top:2993px;width:427px">&#9742; Phone Number</div>
  <div class="abs submit"><svg width="18" height="18" viewBox="0 0 20 20"><path d="M1 9l18-8-6 18-3-7z" fill="#fff"/></svg>Submit</div>
</form>

<footer class="abs site-footer" role="img" aria-label="Dark aerial view of a container port"></footer>
<svg class="abs" style="left:0;top:3170px" width="1200" height="120" viewBox="0 0 1200 120">
  <path d="M0 0 L1200 0 L1200 10 Q600 140 0 10Z" fill="#eef0f3"/>
  <path d="M140 30 Q600 120 1060 30" stroke="#27b5dc" stroke-width="6" fill="none"/>
  <circle cx="600" cy="83" r="24" fill="#fff" stroke="#27b5dc" stroke-width="3"/>
  <circle cx="600" cy="83" r="8" fill="#2f4b9e"/>
</svg>
<div class="abs footer-brand">
  <div class="brand-name">Tarvolen</div>
  <div class="brand-tag">Border Flow Reshaping Trade</div>
</div>
<nav class="abs footer-nav">Home<span>|</span>Products<span>|</span>Web App<span>|</span>About Us<span>|</span>Working At Tarvolen<span>|</span>News<span>|</span>Contact Us</nav>
<p class="abs copyright">© Tarvolen 2019. All rights reserved</p>
<div class="abs social"><span></span><span></span><span></span><span></span></div>

</body>
</html>
```